VENTURE CAPITAL GROUP BUSINESS CARD DESIGN

Venture Capital Group based in SF looking for a bold business card design. No trendy colour explosion, 3D effects etc. Just "simple" optical effects. Works on your brain, keeps your eye focused and sticks to your mind.
Target Market(s)
Technology startups
Industry/Entity Type
Venture Capital
Contact Information for Business Card
DESMOND WHITLAKE
MANAGING PARTNER
187 FENWORTH ST SAN FRANCISCO, CA 94187
415.555.0142 O
415.555.0147 F
415.555.0193 C
desmond@veldtmoorcapital.ventures

```html
<!DOCTYPE html>
<html lang="en">
<head>
<meta charset="utf-8">
<title>Veldtmoor Capital Group — Business Card</title>
<link href="https://fonts.googleapis.com/css2?family=Cinzel:wght@400&family=Saira+Semi+Condensed:wght@600&family=Merriweather:wght@300&display=swap" rel="stylesheet">
<style>
  :root {
    --backdrop: #e6e5e6;
    --card-dark: #151719;
    --card-light: #fafafa;
    --green: #1f8a3a;
    --green-deep: #136b2e;
    --grey-text: #6b6b6b;
    --grey-soft: #8c8c8c;
    --circle-dark: #2a2b2d;
    --circle-light: #ececec;
  }
  * { margin: 0; padding: 0; box-sizing: border-box; }
  html, body { width: 1200px; height: 1200px; overflow: hidden; }
  body { background: var(--backdrop); position: relative; }

  .card { position: absolute; left: 243px; width: 714px; height: 422px; }
  .card-front { top: 110px; background: var(--card-dark); }
  .card-back { top: 668px; background: var(--card-light); }

  /* front */
  .front-badge {
    position: absolute; left: 50%; top: 72px; width: 170px; height: 170px;
    margin-left: -85px; border-radius: 50%;
    background: radial-gradient(circle at 50% 45%, #3a3b3e, var(--circle-dark) 70%, #1d1e20);
  }
  .front-wordmark {
    position: absolute; left: 0; right: 0; top: 286px; text-align: center;
    font-family: "Cinzel", serif; font-weight: 400; color: var(--green);
  }
  .front-wordmark .name { display: block; font-size: 50px; letter-spacing: 1px; line-height: 1; }
  .front-wordmark .group { display: block; font-size: 14px; letter-spacing: 7px; margin-top: 6px; }

  /* back */
  .back-badge {
    position: absolute; left: 50px; top: 126px; width: 170px; height: 170px; border-radius: 50%;
    background: radial-gradient(circle at 50% 40%, #ffffff, var(--circle-light) 75%, #dcdcdc);
    display: flex; align-items: center; justify-content: center;
  }
  .back-badge .name {
    font-family: "Merriweather", serif; font-weight: 300; font-size: 22px; color: var(--green);
  }
  .contact-block { position: absolute; left: 330px; top: 96px; }
  .person-name {
    font-family: "Saira Semi Condensed", sans-serif; font-weight: 600;
    font-size: 28px; color: var(--green-deep); line-height: 1.1;
  }
  .person-title {
    font-family: "Merriweather", serif; font-weight: 300; font-size: 15px;
    color: var(--grey-text); margin-top: 4px;
  }
  .contact-list { list-style: none; margin-top: 40px; }
  .contact-list li {
    display: flex; align-items: center; height: 22px;
    font-family: "Merriweather", serif; font-weight: 300; font-size: 16px; color: var(--grey-text);
  }
  .contact-list .icon { width: 18px; height: 16px; margin-right: 16px; fill: var(--green-deep); flex: none; }
  .contact-list .accent { color: var(--green); }
  .address {
    font-family: "Merriweather", serif; font-weight: 300; font-size: 16px;
    color: var(--grey-text); margin-top: 8px;
  }
</style>
</head>
<body>

<section class="card card-front">
  <div class="front-badge"></div>
  <div class="front-wordmark">
    <span class="name">VELDTMOOR</span>
    <span class="group">CAPITAL GROUP</span>
  </div>
</section>

<section class="card card-back">
  <div class="back-badge"><span class="name">Veldtmoor</span></div>

  <div class="contact-block">
    <h1 class="person-name">Desmond Whitlake</h1>
    <p class="person-title">Managing Partner</p>

    <ul class="contact-list">
      <li>
        <svg class="icon" viewBox="0 0 18 16"><path d="M1 5c0-2 4-3 8-3s8 1 8 3v1.5h-4V5H5v1.5H1z"/><path d="M4 8l2-1.5h6L14 8v6H4z"/></svg>
        415.555.0142
      </li>
      <li>
        <svg class="icon" viewBox="0 0 18 16"><rect x="5" y="1" width="8" height="4"/><rect x="1" y="5.5" width="16" height="6" rx="1"/><rect x="5" y="10" width="8" height="5"/></svg>
        415.555.0147
      </li>
      <li>
        <svg class="icon" viewBox="0 0 18 16"><rect x="5" y="0.5" width="8" height="15" rx="1.5"/><rect x="6.5" y="2.5" width="5" height="9" fill="#fafafa"/></svg>
        415.555.0193
      </li>
      <li>
        <svg class="icon" viewBox="0 0 18 16"><rect x="1" y="3" width="16" height="11"/><path d="M1 3l8 6 8-6" fill="none" stroke="#fafafa" stroke-width="1.4"/><path d="M1 14l6-5M17 14l-6-5" stroke="#fafafa" stroke-width="1.2"/></svg>
        desmond@veldtmoorcapital.ventures
      </li>
      <li>
        <svg class="icon" viewBox="0 0 18 16"><circle cx="9" cy="8" r="7"/><path d="M2 8h14M9 1v14M4 3.5c3 2 7 2 10 0M4 12.5c3-2 7-2 10 0" fill="none" stroke="#fafafa" stroke-width="1"/><ellipse cx="9" cy="8" rx="3" ry="7" fill="none" stroke="#fafafa" stroke-width="1"/></svg>
        www.<span class="accent">veldtmoorcapital</span>.ventures
      </li>
    </ul>

    <p class="address">187 Fenworth St San Francisco, CA 94187</p>
  </div>
</section>

</body>
</html>
```